Brochure condensed from the PDF marketing

An organised brochure with 4 x banner heading for the various portfolios,
Condensed and made into a 4 page booklet or neat and tidy brochure display that can be easily emailed to prospective customers. The brochure should be neat and professional similar content to the website to send the 4 x Portfolios to the various Industry Categories, thank you

** Ive just uploaded a couple of extra photos for the ' Our Services ' area on the Brochure, pls add the ice cream one for the ' Parfait Cleaning and Sanitisation Services, and on the ' Our Services' category for the High pressure Gurney and Playground Cleaning pls add a fun photo for example the one I sent with people having fun on the playground equipment, **

HI KT Designer The brochure design is for my facebook title page /Users/user/Desktop/Screenshot 2020-05-05 at 9.22.39 PM.png Under Brightwell Facebook Design (Contest) DO you have a direct email, its very difficult to keep posing images and updates here Thank you Imogen @ Brightwell.

Target Market(s)

Cleaning Services

Font styles to use
Serif

Requirements
Must have
• Look professional and neat and tidy brochure booklet for marketing on email to prospective customers.

```html
<!DOCTYPE html>
<html lang="en">
<head>
<meta charset="utf-8">
<title>Brightwell Brochure</title>
<link rel="stylesheet" href="https://fonts.googleapis.com/css2?family=Noto+Serif:wght@400;700&family=Roboto+Condensed:wght@300;400;700&display=swap">
<style>
:root{
  --orange:#ef5a12;
  --orange-band:rgba(238,88,18,.92);
  --navy:#13417f;
  --navy-deep:#123a78;
  --ink:#1d3f76;
  --paper:#f4f4f5;
  --stage-top:#a4a4a6;
  --stage-bottom:#c6c6c8;
  --serif:'Noto Serif',Georgia,serif;
  --sans:'Roboto Condensed',Arial,sans-serif;
}
*{margin:0;padding:0;box-sizing:border-box}
html,body{width:1200px;height:2769px;overflow:hidden}
body{position:relative;background:var(--stage-bottom);font-family:var(--sans);color:var(--ink)}
.stage-top{position:absolute;left:0;top:0;width:1200px;height:1130px;background:radial-gradient(ellipse at 50% 40%,#b4b4b6,var(--stage-top))}
.page{position:absolute;width:522px;height:738px;background:var(--paper);overflow:hidden;box-shadow:0 4px 14px rgba(0,0,0,.25)}
.cover-hero{left:327px;top:178px;transform:scale(1.082);transform-origin:0 0}
.cover-flat{left:61px;top:1195px}
.page-intro{left:610px;top:1195px}
.page-services{left:61px;top:1962px}
.page-back{left:613px;top:1962px;background:var(--navy-deep)}

/* brand head */
.wordmark{display:flex;align-items:center;gap:10px}
.mark-square{width:26px;height:26px;background:var(--orange)}
.wordmark .name{font-family:var(--serif);font-size:46px;color:var(--navy);line-height:1}
.brand-head{position:absolute;left:96px;top:28px}
.brand-head .url{font-family:var(--serif);font-size:13.5px;letter-spacing:4.2px;color:var(--ink);margin:4px 0 0 36px}
.accent-rule{position:absolute;left:52px;right:0;top:128px;height:7px;background:var(--orange)}

/* portfolio grid */
.portfolio{position:absolute;left:0;width:522px}
.row-a{top:135px;height:214px}
.row-b{top:349px;height:204px}
.photo{position:absolute;inset:0}
.row-a .photo.left{background:linear-gradient(160deg,#6b4a35,#c9a880 60%,#3d3a38);clip-path:polygon(0 0,62% 0,53% 100%,0 100%)}
.row-a .photo.right{background:linear-gradient(200deg,#e8e9eb,#9aa4b3 55%,#3e4c6a);clip-path:polygon(62% 0,100% 0,100% 100%,53% 100%)}
.row-b .photo.left{background:linear-gradient(170deg,#d8d4cc,#8a7a6a 55%,#5d4a3d);clip-path:polygon(0 0,58% 0,47% 100%,0 100%)}
.row-b .photo.right{background:linear-gradient(190deg,#7aa1c8,#c43a3a 55%,#3b3f7a);clip-path:polygon(58% 0,100% 0,100% 100%,47% 100%)}
.band{position:absolute;left:0;right:0;bottom:0;height:54px;background:var(--orange-band)}
.label{position:absolute;top:10px;color:#fff;font-size:15px;font-weight:300;line-height:1.1}
.label b{display:block;font-weight:700;font-size:17px}
.label.l{left:24px}
.label.r{right:22px;text-align:right}
.slash{position:absolute;inset:0;pointer-events:none}

.welcome{position:absolute;left:0;right:0;top:553px;bottom:0;background:linear-gradient(180deg,#fff,#ececee);text-align:center}
.welcome h1{font-family:var(--serif);font-weight:400;color:var(--navy);font-size:40px;line-height:1;margin-top:36px}
.welcome h1 b{display:block;font-size:54px;font-weight:700;letter-spacing:1px;margin-top:2px}
.welcome .contact{font-family:var(--serif);font-size:13.5px;color:var(--ink);margin-top:12px}

/* intro page */
.hero-shape{position:absolute;left:0;top:0;width:230px;height:250px;background:radial-gradient(circle at 40% 40%,#8a98a8,#5a6676);border-radius:0 0 60% 40%/0 0 50% 60%}
.intro-head{position:absolute;left:265px;top:62px;width:230px}
.intro-head h2{font-family:var(--serif);font-size:18px;line-height:1;color:var(--navy)}
.intro-head h2 em{font-style:normal;color:var(--orange)}
.intro-head .since{font-size:9.5px;color:var(--orange);margin:12px 0 12px}
.intro-head p{font-size:9.5px;line-height:1.3;text-align:justify;color:var(--ink)}
.pillars{position:absolute;left:26px;top:279px;display:flex;gap:7px}
.pillar{width:153px;height:279px;background:var(--navy)}
.pillar .icon{height:78px;background:var(--orange);display:flex;align-items:center;justify-content:center}
.pillar h3{font-family:var(--serif);color:#fff;font-size:13px;text-align:center;margin:20px 0 8px}
.pillar p{color:#fff;font-size:9px;line-height:1.28;text-align:center;padding:0 12px}
.values{position:absolute;left:26px;top:575px;width:475px}
.values h3{font-family:var(--serif);font-size:18px;color:var(--orange);margin-bottom:8px}
.values p{font-size:8.2px;line-height:1.7;color:var(--navy)}
.values b{font-weight:700}
.page-foot{position:absolute;left:22px;right:0;top:698px;display:flex;align-items:center;gap:8px}
.page-foot .mini-square{width:14px;height:14px;background:var(--orange)}
.page-foot .name{font-family:var(--serif);font-size:19px;color:var(--navy)}
.page-foot .rule{flex:1;height:1px;background:var(--navy)}
.page-foot .num{width:22px;height:22px;background:var(--orange);color:#fff;font-family:var(--serif);font-size:13px;text-align:center;line-height:22px;margin-right:24px}

/* services page */
.section-title{font-family:var(--serif);font-size:18px;color:var(--navy);text-align:center;font-weight:700}
.section-title em{font-style:normal;color:var(--orange)}
.services-title{position:absolute;left:0;right:0;top:22px}
.service-tiles{position:absolute;left:26px;top:52px;display:flex;gap:16px}
.tile{width:106px;text-align:center}
.tile .shot{height:103px;border:4px solid #fff;box-shadow:0 1px 4px rgba(0,0,0,.3)}
.tile p{font-family:var(--serif);font-size:10px;font-weight:700;line-height:1.2;color:var(--navy);margin-top:10px}
.safety{position:absolute;left:0;right:0;top:222px;height:190px;background:var(--navy);color:#fff;text-align:center;padding:12px 30px 0}
.safety .section-title{color:#fff}
.safety p{font-size:8.4px;line-height:1.3;margin-top:9px}
.pricing-title{position:absolute;left:0;right:0;top:420px}
.price-grid{position:absolute;left:26px;top:446px;display:flex;gap:6px}
.price{width:73px;height:86px;border:1px solid var(--navy);background:#fff;padding:4px}
.price h4{font-family:var(--serif);font-size:6.6px;color:var(--navy);line-height:1.15;height:26px}
.price .amt{font-family:var(--serif);font-size:10px;font-weight:700;color:var(--orange);margin-top:4px}
.price small{display:block;font-size:5px;color:#777}
.price-note{position:absolute;left:26px;top:538px;font-size:6.5px;color:var(--navy)}
.stories{position:absolute;left:26px;top:560px;width:330px}
.stories h3{font-family:var(--serif);font-size:18px;color:var(--navy)}
.stories h3 em{font-style:normal;color:var(--orange)}
.stories p{font-size:7.4px;line-height:1.3;color:var(--navy);margin-top:4px}
.client-name{position:absolute;left:380px;top:615px;display:flex;align-items:center;gap:6px}
.client-name .sq{width:30px;height:30px;background:#c8102e}
.client-name span{font-family:var(--serif);font-size:13px;font-weight:700;color:var(--navy);line-height:1.1}

/* back page */
.back-brand{position:absolute;left:0;right:0;top:78px;display:flex;justify-content:center;align-items:center;gap:10px}
.back-brand .mark-square{width:24px;height:24px}
.back-brand .name{font-family:var(--serif);font-size:40px;color:#fff}
.back-contact{position:absolute;left:0;right:0;top:164px;text-align:center;font-family:var(--serif);color:#fff;font-size:14px;line-height:1.22}
.back-glow{position:absolute;left:-40px;top:300px;width:600px;height:460px;background:radial-gradient(ellipse at 50% 50%,rgba(255,255,255,.05),transparent 70%)}
</style>
</head>
<body>

<div class="stage-top"></div>

<!-- Cover, featured -->
<article class="page cover-hero">
  <header class="brand-head">
    <div class="wordmark"><span class="mark-square"></span><span class="name">Brightwell</span></div>
    <div class="url">www.brightwell.com.au</div>
  </header>
  <div class="accent-rule"></div>
  <section class="portfolio row-a">
    <div class="photo left" role="img" aria-label="Commercial kitchen equipment being cleaned"></div>
    <div class="photo right" role="img" aria-label="Office cleaning staff at work"></div>
    <div class="band">
      <p class="label l">EQUIPMENT CLEANING &amp;<b>SANITISATION SERVICES</b></p>
      <p class="label r">GENERAL CLEANING &amp; PROPERTY<b>FACILITIES MANAGEMENT</b></p>
    </div>
    <svg class="slash" viewBox="0 0 522 214" preserveAspectRatio="none"><line x1="324" y1="0" x2="277" y2="214" stroke="#fff" stroke-width="3"/></svg>
  </section>
  <section class="portfolio row-b">
    <div class="photo left" role="img" aria-label="Kitchen detail cleaning of dishes"></div>
    <div class="photo right" role="img" aria-label="Family having fun on playground equipment"></div>
    <div class="band">
      <p class="label l">KITCHEN DETAIL CLEANING<b>SERVICES</b></p>
      <p class="label r">HIGH PRESSURE GURNEY &amp; PLAYGROUND<b>CLEANING SERVICES</b></p>
    </div>
    <svg class="slash" viewBox="0 0 522 204" preserveAspectRatio="none"><line x1="303" y1="0" x2="245" y2="204" stroke="#fff" stroke-width="3"/></svg>
  </section>
  <section class="welcome">
    <h1>Welcome to<b>BRIGHTWELL</b></h1>
    <p class="contact">Customer Service: 1300 555 018 &nbsp;|&nbsp; Email: service@brightwell.com.au</p>
  </section>
</article>

<!-- Cover, spread -->
<article class="page cover-flat">
  <header class="brand-head">
    <div class="wordmark"><span class="mark-square"></span><span class="name">Brightwell</span></div>
    <div class="url">www.brightwell.com.au</div>
  </header>
  <div class="accent-rule"></div>
  <section class="portfolio row-a">
    <div class="photo left" role="img" aria-label="Commercial kitchen equipment being cleaned"></div>
    <div class="photo right" role="img" aria-label="Office cleaning staff at work"></div>
    <div class="band">
      <p class="label l">EQUIPMENT CLEANING &amp;<b>SANITISATION SERVICES</b></p>
      <p class="label r">GENERAL CLEANING &amp; PROPERTY<b>FACILITIES MANAGEMENT</b></p>
    </div>
    <svg class="slash" viewBox="0 0 522 214" preserveAspectRatio="none"><line x1="324" y1="0" x2="277" y2="214" stroke="#fff" stroke-width="3"/></svg>
  </section>
  <section class="portfolio row-b">
    <div class="photo left" role="img" aria-label="Kitchen detail cleaning of dishes"></div>
    <div class="photo right" role="img" aria-label="Family having fun on playground equipment"></div>
    <div class="band">
      <p class="label l">KITCHEN DETAIL CLEANING<b>SERVICES</b></p>
      <p class="label r">HIGH PRESSURE GURNEY &amp; PLAYGROUND<b>CLEANING SERVICES</b></p>
    </div>
    <svg class="slash" viewBox="0 0 522 204" preserveAspectRatio="none"><line x1="303" y1="0" x2="245" y2="204" stroke="#fff" stroke-width="3"/></svg>
  </section>
  <section class="welcome">
    <h1>Welcome to<b>BRIGHTWELL</b></h1>
    <p class="contact">Customer Service: 1300 555 018 &nbsp;|&nbsp; Email: service@brightwell.com.au</p>
  </section>
</article>

<!-- Page 1 -->
<article class="page page-intro">
  <div class="hero-shape" role="img" aria-label="Carpet cleaning in progress with blue shoe covers"></div>
  <div class="intro-head">
    <h2>WORKING<br>WITH <em>BRIGHTWELL</em></h2>
    <p class="since">We have been in business for 15 years.</p>
    <p>Our people are professional, reliable and service orientated. In every interaction on site, receiving help from our service support staff or rolling-out new cleaning sites, we are focused on delivering a positive &amp; high quality customer service experience.</p>
  </div>
  <div class="pillars">
    <div class="pillar">
      <div class="icon"><svg width="40" height="44" viewBox="0 0 40 44" fill="none" stroke="#fff" stroke-width="2"><circle cx="20" cy="12" r="5"/><circle cx="11" cy="20" r="4"/><circle cx="29" cy="20" r="4"/><path d="M20 17v14M8 31h24l-3 10H11z"/></svg></div>
      <h3>OUR PURPOSE</h3>
      <p>Our purpose is to provide high quality hygiene and sanitisation services to each of our dedicated portfolios across equipment cleaning services, gurney and playground cleaning, general commercial cleaning and property facility maintenance services to create the most effective results for our customers and community.</p>
    </div>
    <div class="pillar">
      <div class="icon"><svg width="50" height="50" viewBox="0 0 50 50" fill="#fff"><path d="M25 0l4 21 21 4-21 4-4 21-4-21L0 25l21-4z"/></svg></div>
      <h3>OUR VISION</h3>
      <p>Sustainable commercial environment and food service equipment cleaning and sanitisation service provider.Recognised as being the most effective brand, growing employees and giving back to the community for generations to come.</p>
    </div>
    <div class="pillar">
      <div class="icon"><svg width="54" height="54" viewBox="0 0 54 54" fill="none" stroke="#fff" stroke-width="2"><circle cx="27" cy="27" r="24"/><path d="M27 6v4M27 44v4M6 27h4M44 27h4"/><path d="M36 18l-6 12-12 6 6-12z" fill="#fff"/></svg></div>
      <h3>OUR STRATEGY</h3>
      <p>To differentiate ourselves through a prevailing focus on customer service, in everything we do and every interaction we have to be a positive and professional experience. We treat our people as skilled cleaning professionals who are the foundation of our companys sustainability.</p>
    </div>
  </div>
  <div class="values">
    <h3>OUR VALUES</h3>
    <p><b>Safety and the Environment</b> – We are committed to providing a safe and healthy working environment.<br>
    <b>Professionalism/Integrity</b> – We are committed to doing what we say we are going to do.<br>
    <b>Sustainability</b> – Achieving results that are mutually beneficial for our employees, our customers, our partners and the company.<br>
    <b>Positive Working Relationships</b> – Having relationships that focus on shared goals and creation of value for all parties.<br>
    <b>Respect for Each Other</b> – The embracing of diversity, enriched by openness, sharing, trust, teamwork and involvement.</p>
  </div>
  <footer class="page-foot"><span class="mini-square"></span><span class="name">Brightwell</span><span class="rule"></span><span class="num">1</span></footer>
</article>

<!-- Page 2 -->
<article class="page page-services">
  <h2 class="section-title services-title">OUR <em>SERVICES</em></h2>
  <div class="service-tiles">
    <div class="tile"><div class="shot" role="img" aria-label="Ice cream machine being serviced" style="background:linear-gradient(160deg,#3f5c8a,#9bb0c8)"></div><p>Equipment Cleaning &amp; Sanitisation Services</p></div>
    <div class="tile"><div class="shot" role="img" aria-label="Office cleaners at work" style="background:linear-gradient(160deg,#eef0f2,#9fb3c6)"></div><p>General Cleaning &amp; Property Facilities Management</p></div>
    <div class="tile"><div class="shot" role="img" aria-label="High pressure cleaning of a garden path" style="background:linear-gradient(160deg,#5c6b3a,#a39a7a)"></div><p>High Pressure gurney &amp; play ground equipment Cleaning</p></div>
    <div class="tile"><div class="shot" role="img" aria-label="Chefs in a commercial kitchen" style="background:linear-gradient(160deg,#d8d8d8,#6c6c70)"></div><p>Kitchen Detail Cleaning Service</p></div>
  </div>
  <section class="safety">
    <h2 class="section-title">SAFETY &amp; <em>COMPLIANCE</em></h2>
    <p>Brightwell values safety and environment. We have an overriding commitment to health, safety and environmental responsibility.</p>
    <p>Each member of our company community undergoes a yearly on-line safety refresher course, and performs a routine reflection safety check and risk assessment at each clients site on attending work each day. We have safety work method statements in place and work on ensuring our people work safely on site through practical application of safety steps, safety shoes and appropriate personal protection equipment (PPE) work gear.</p>
    <p>Brightwell is covered with $20,000,000 General and Product Liability coverage through Harbourline Insurance LTD and has work cover in place for all our employees across Sydney, Brisbane, Melbourne and Adelaide.</p>
    <p>Brightwell employees always aspire to work safely whilst on client sites.</p>
  </section>
  <h2 class="section-title pricing-title">CURRENT <em>PRICING</em></h2>
  <div class="price-grid">
    <div class="price"><h4>General Office Cleaning</h4><div class="amt">$ 70.00</div><small>+ GST/hour</small></div>
    <div class="price"><h4>Parfait Equipment Cleaning Single Unit</h4><div class="amt">$ 120.00</div><small>+ GST/service</small></div>
    <div class="price"><h4>Parfait Equipment Cleaning Double Unit</h4><div class="amt">$ 180.00</div><small>+ GST/fortnightly service</small><div class="amt">$ 200.00</div><small>+ GST/monthly service</small></div>
    <div class="price"><h4>Gurney High Pressure work</h4><div class="amt">$ 100.00</div><small>+ GST/hour</small></div>
    <div class="price"><h4>Builders Cleaning Services</h4><div class="amt">$ 100.00</div><small>+ GST/hour</small><small>* + Any rubbish removal fee for waste disposal</small></div>
    <div class="price"><h4>Kitchen Detail Foam and Scrub</h4><div class="amt">$ 80.00</div><small>+ GST/hour</small></div>
  </div>
  <p class="price-note">* &gt; 50km travel fee and public holiday rates apply in accordance to the Brightwell Services Award, 2010.</p>
  <section class="stories">
    <h3>OUR <em>SUCCESS STORIES</em></h3>
    <p>Project Management</p>
    <p>We successfully managed the roll out of 200 Equipment Asset Parfait Whirler Machines, 191 K Vellano Machines for Crestline Chicken from 2012 to 2019 for the facilities department. We resourced the project with the most effective talent including skilled mechanics, mechanical engineers and professional tradespeople.</p>
    <p>Brightwell was responsible for the regular fortnightly cleaning and maintenance sanitisation services including regular 6 monthly tune up kit installations for the Crestline Chicken Community across, Sydney, Brisbane, Melbourne and Adelaide.</p>
  </section>
  <div class="client-name"><span class="sq"></span><span>Crestline<br>Chicken</span></div>
  <footer class="page-foot"><span class="mini-square"></span><span class="name">Brightwell</span><span class="rule"></span><span class="num">2</span></footer>
</article>

<!-- Back page -->
<article class="page page-back">
  <div class="back-glow"></div>
  <div class="back-brand"><span class="mark-square"></span><span class="name">Brightwell</span></div>
  <address class="back-contact" style="font-style:normal">
    Sydney | Brisbane | Melbourne | Adelaide<br>
    Harlow, QLD, 4150<br>
    Landline: 1300 555 018<br>
    Mobile: 0400 555 274<br>
    Email: service@brightwell.com.au<br>
    www.brightwell.com.au
  </address>
</article>

</body>
</html>
```